Car transport business

We need a new business card design. Attached is our old card sample. I would just like to adjust the logo colors (blue and red) to be brighter. I changed my name to the brighter red and the word dispatcher to a brighter blue as an example. But you can adjust those colors further. And then perhaps you can use the same colors for the card design but use your imagination.

As a suggestion so the card stands out I would like to add a clip art of car carrier truck. Attached are examples of that as well

```html
<!DOCTYPE html>
<html lang="en">
<head>
<meta charset="utf-8">
<title>Vale Haul – Business Card</title>
<link rel="stylesheet" href="https://fonts.googleapis.com/css2?family=Montserrat:wght@400;500;800&display=swap">
<style>
  :root {
    --backdrop: #dcdcdc;
    --card-white: #ffffff;
    --brand-blue: #165a87;
    --brand-red: #c11f2d;
    --emboss-blue: #0f4a72;
    --accent-blue: #3b9ee6;
  }
  * { margin: 0; padding: 0; box-sizing: border-box; }
  html, body {
    width: 1200px; height: 1200px; overflow: hidden;
    background: var(--backdrop);
    font-family: "Montserrat", Arial, sans-serif;
  }
  .card {
    position: absolute; left: 207px; width: 786px; height: 449px;
    overflow: hidden;
  }
  .card-front { top: 112px; background: var(--card-white); }
  .card-back { top: 640px; background: var(--brand-blue); }

  .brand { position: absolute; left: 420px; top: 82px; width: 316px; text-align: right; }
  .brand-name {
    font-weight: 800; font-size: 30px; letter-spacing: 0.5px;
    color: var(--brand-blue); line-height: 1;
  }
  .brand-tagline {
    font-weight: 500; font-size: 9.2px; letter-spacing: 2.2px;
    color: var(--brand-blue); margin-top: 5px; white-space: nowrap;
  }
  .brand-mark {
    position: absolute; left: 424px; top: 45px; width: 44px; height: 44px;
    border-radius: 50%; background: var(--brand-red);
  }

  .name-bar { position: absolute; left: 0; top: 229px; width: 11px; height: 53px; background: var(--brand-blue); }
  .person-name {
    position: absolute; left: 48px; top: 222px;
    font-weight: 500; font-size: 42px; color: var(--brand-red); line-height: 1;
  }
  .person-role {
    position: absolute; left: 49px; top: 263px;
    font-weight: 400; font-size: 20px; color: var(--brand-blue); letter-spacing: 0.3px;
  }
  .divider { position: absolute; left: 49px; top: 305px; width: 687px; height: 1px; background: var(--brand-red); }

  .contact-list { position: absolute; left: 49px; top: 324px; list-style: none; }
  .contact-item {
    display: flex; align-items: center; height: 25.5px;
    font-size: 20px; color: var(--brand-blue);
  }
  .contact-icon { width: 16px; height: 16px; margin-right: 6px; fill: var(--brand-red); }

  .back-mark {
    position: absolute; left: 133px; top: 166px; width: 70px; height: 70px;
    border-radius: 50%; background: var(--accent-blue);
  }
  .back-text { position: absolute; left: 215px; top: 230px; }
  .back-name { font-weight: 800; font-size: 46px; color: var(--emboss-blue); line-height: 1; letter-spacing: 1px; }
  .back-tagline { font-weight: 500; font-size: 14px; letter-spacing: 4px; color: var(--emboss-blue); margin-top: 4px; white-space: nowrap; }
</style>
</head>
<body>
  <section class="card card-front">
    <div class="brand-mark"></div>
    <div class="brand">
      <div class="brand-name">VALE HAUL</div>
      <div class="brand-tagline">CAR CARRIER SHIPPING SPECIALISTS</div>
    </div>

    <div class="name-bar"></div>
    <h1 class="person-name">RORY BENNET</h1>
    <p class="person-role">DISPATCHER</p>
    <div class="divider"></div>

    <ul class="contact-list">
      <li class="contact-item">
        <svg class="contact-icon" viewBox="0 0 16 16" aria-hidden="true"><path d="M4 1 L6.5 4.5 L5 6 C6 8.5 7.5 10 10 11 L11.5 9.5 L15 12 L13 15 C7 14.5 1.5 9 1 3 Z"/></svg>
        555-014-2837
      </li>
      <li class="contact-item">
        <svg class="contact-icon" viewBox="0 0 16 16" aria-hidden="true"><rect x="4" y="1" width="8" height="4"/><rect x="1" y="5" width="14" height="7" rx="1"/><rect x="4" y="10" width="8" height="5" fill="#fff" stroke="#c11f2d" stroke-width="1.2"/></svg>
        555-014-2900
      </li>
      <li class="contact-item">
        <svg class="contact-icon" viewBox="0 0 16 16" aria-hidden="true"><rect x="1.5" y="3.5" width="13" height="9" fill="none" stroke="#c11f2d" stroke-width="1.4"/><path d="M1.5 3.5 L8 9 L14.5 3.5" fill="none" stroke="#c11f2d" stroke-width="1.4"/></svg>
        valehaul@example.com
      </li>
    </ul>
  </section>

  <section class="card card-back">
    <div class="back-mark"></div>
    <div class="back-text">
      <div class="back-name">VALE HAUL</div>
      <div class="back-tagline">CAR CARRIER SHIPPING SPECIALISTS</div>
    </div>
  </section>
</body>
</html>
```